Music Studio and Store Business Card and Logo Design

We need a business card and logo design for an existing Music Studio (Piano and Voice) which will soon expand to offer retail sheet music for all instruments including voice. The expanding store will not sell or lease instruments. We are a well known Fine Arts Studio for instruction to children, college students, and adults with 42 enrolled students and a wait list. We want something with simple elegance, but not archaic. Even a sleek modern look is okay. We do not want something childish or too fun looking because we do serve ages 5 - 62. We would also like the logo workable/transferable to signage for our new location opening in March. We like classic burgundy, black, deep blues, but are open to other suggestions. We included our studio brochure so you can get to know us a little better and some images we thought were interesting with the use of clef signs for the & and using note heads for the bottom or top of the letter "H"

Target Market(s)

All ages

Industry/Entity Type

Business

Contact Information for Business Card

H&H Music StudioPlattsburgh, NYWanda J. Haby and Oren M. Castaldi, Owners

Requirements
Must have
• Phone Number: (555) 817-4062
• Website: www.rbtonalartsroom.example
Nice to have
• Email: lorna@rbtonalartsroom.example
Should not have
• Any instruments on the card other than piano. Instrument pix is not a necessity.

```html
<!DOCTYPE html>
<html lang="en">
<head>
<meta charset="utf-8">
<title>R&amp;B Music Studio – Business Card</title>
<link rel="stylesheet" href="https://fonts.googleapis.com/css2?family=Source+Sans+3:wght@400;600;700&display=swap">
<style>
  :root {
    --studio-red: #ff0a0a;
    --card-white: #ffffff;
    --ink-black: #111111;
    --backdrop: #ecebe8;
    --card-shadow: rgba(0, 0, 0, 0.18);
  }
  * { box-sizing: border-box; margin: 0; padding: 0; }
  html, body {
    width: 1200px;
    height: 900px;
    overflow: hidden;
  }
  body {
    background: var(--backdrop);
    font-family: "Source Sans 3", "Helvetica Neue", Arial, sans-serif;
    position: relative;
  }
  .card {
    position: absolute;
    width: 540px;
    height: 309px;
    top: 296px;
    border-radius: 2px;
    overflow: hidden;
    box-shadow: 0 10px 28px var(--card-shadow);
  }
  .card--front {
    left: 40px;
    background: var(--studio-red);
    display: flex;
    align-items: center;
    justify-content: center;
  }
  .card--back {
    left: 620px;
    background: var(--studio-red);
  }
  .wordmark {
    display: flex;
    align-items: center;
    gap: 12px;
    font-weight: 600;
    font-size: 26px;
    letter-spacing: 0.06em;
    text-transform: uppercase;
    white-space: nowrap;
  }
  .wordmark__dot {
    width: 16px;
    height: 16px;
    border-radius: 50%;
    flex: none;
  }
  .card--front .wordmark { color: var(--card-white); }
  .card--front .wordmark__dot { background: var(--card-white); }
  .back__brand {
    height: 140px;
    background: var(--card-white);
    display: flex;
    align-items: center;
    justify-content: center;
  }
  .card--back .wordmark { color: var(--studio-red); font-size: 24px; }
  .card--back .wordmark__dot { background: var(--ink-black); }
  .back__details {
    height: 169px;
    display: flex;
    flex-direction: column;
    align-items: center;
    justify-content: center;
    color: var(--card-white);
    text-align: center;
  }
  .owner-name {
    font-weight: 700;
    font-size: 18px;
    line-height: 1.2;
  }
  .owner-role {
    font-size: 13px;
    margin-top: 2px;
  }
  .studio-location {
    font-size: 16px;
    margin-top: 6px;
  }
  .contact-list {
    list-style: none;
    margin-top: 8px;
    font-size: 13px;
    line-height: 1.35;
  }
  .contact-list__sep { margin: 0 6px; }
</style>
</head>
<body>
  <section class="card card--front" aria-label="Card front">
    <div class="wordmark">
      <span class="wordmark__dot"></span>
      <span class="wordmark__name">R&amp;B Music Studio</span>
    </div>
  </section>

  <section class="card card--back" aria-label="Card back">
    <div class="back__brand">
      <div class="wordmark">
        <span class="wordmark__dot"></span>
        <span class="wordmark__name">R&amp;B Music Studio</span>
      </div>
    </div>
    <div class="back__details">
      <p class="owner-name">Lorna P. Quist</p>
      <p class="owner-name">Oren M. Castaldi</p>
      <p class="owner-role">Owners</p>
      <p class="studio-location">Millbrook Falls, NY</p>
      <ul class="contact-list">
        <li>(555) 817-4062<span class="contact-list__sep">|</span>www.rbtonalartsroom.example</li>
        <li>lorna@rbtonalartsroom.example</li>
      </ul>
    </div>
  </section>
</body>
</html>
```